Business Card and Simple Logo Desgin

New Zealand based start up company "Vesta Advisory LTD" requires business cards and simple logo design.

Card Content.

Vesta Advisory LTD

Rebecca Thornbury
CA, BMS (Hons)

r.thornbury@vestaadvisory.co.nz
PH +64 21 574 613

Target Market(s)

Corporate Business in IT, Finance and accounting.

Industry/Entity Type

Business

```html
<!DOCTYPE html>
<html lang="en">
<head>
<meta charset="utf-8">
<title>Vesta Advisory LTD — Business Card</title>
<link rel="stylesheet" href="https://fonts.googleapis.com/css2?family=Exo+2:wght@600&family=Roboto:wght@400;500&display=swap">
<style>
  :root {
    --backdrop: #e9e6e1;
    --card: #ffffff;
    --ink: #3a3d40;
    --ink-soft: #6b6f73;
    --brand-blue: #2aa7db;
    --brand-green: #8cc540;
    --pattern-a: #eef5fa;
    --pattern-b: #f3f8ec;
  }
  * { box-sizing: border-box; margin: 0; padding: 0; }
  html, body {
    width: 1200px; height: 900px; overflow: hidden;
    background: var(--backdrop);
  }
  .sheet {
    width: 1200px; height: 900px;
    display: flex; flex-direction: column; align-items: center; justify-content: center;
    gap: 40px;
  }
  .card {
    position: relative;
    width: 700px; height: 400px;
    background: var(--card);
    box-shadow: 0 10px 28px rgba(0,0,0,0.18);
    overflow: hidden;
  }
  .card__pattern {
    position: absolute; top: 0; right: 0; width: 62%; height: 82%;
    background: linear-gradient(135deg, var(--pattern-a), var(--pattern-b) 60%, rgba(255,255,255,0));
  }
  .card__band {
    position: absolute; left: 0; bottom: 0; width: 100%; height: 70px;
  }
  .card__band svg { display: block; width: 100%; height: 100%; }

  .wordmark {
    font-family: "Exo 2", sans-serif;
    font-weight: 600;
    color: var(--ink);
    text-transform: uppercase;
    letter-spacing: 0.01em;
    display: flex; align-items: center; gap: 14px;
  }
  .wordmark__square {
    background: var(--brand-blue);
    flex: none;
  }

  .card--front .wordmark {
    position: absolute; left: 80px; top: 150px;
    font-size: 46px;
  }
  .card--front .wordmark__square { width: 34px; height: 34px; }

  .card--back .wordmark {
    position: absolute; left: 60px; top: 60px;
    font-size: 22px; gap: 10px;
  }
  .card--back .wordmark__square { width: 18px; height: 18px; }

  .holder {
    position: absolute; left: 90px; top: 140px;
    font-family: "Roboto", sans-serif;
  }
  .holder__name {
    color: var(--brand-blue);
    font-weight: 500; font-size: 21px;
    text-transform: uppercase; letter-spacing: 0.02em;
  }
  .holder__title {
    color: var(--ink-soft);
    font-size: 13px; margin-top: 4px;
    text-transform: uppercase;
  }
  .contact {
    list-style: none;
    margin-top: 30px;
    font-family: "Roboto", sans-serif;
    font-size: 13px; line-height: 1.75;
    color: var(--ink-soft);
    text-transform: uppercase; letter-spacing: 0.02em;
  }
  .contact__key { color: var(--brand-green); font-weight: 500; margin-right: 8px; }
</style>
</head>
<body>
<main class="sheet">

  <section class="card card--front" aria-label="Card front">
    <div class="card__pattern" role="img" aria-label="Faint blue and green background pattern"></div>
    <div class="wordmark"><span class="wordmark__square"></span>Vesta Advisory LTD</div>
    <div class="card__band">
      <svg viewBox="0 0 700 70" preserveAspectRatio="none" aria-hidden="true">
        <rect x="0" y="44" width="700" height="26" fill="var(--brand-blue)"/>
        <path d="M540 44 L540 18 Q540 0 558 0 L700 0 L700 44 Z" fill="var(--brand-green)"/>
      </svg>
    </div>
  </section>

  <section class="card card--back" aria-label="Card back">
    <div class="card__pattern" role="img" aria-label="Faint blue and green background pattern"></div>
    <div class="wordmark"><span class="wordmark__square"></span>Vesta Advisory LTD</div>
    <div class="holder">
      <p class="holder__name">Rebecca Thornbury</p>
      <p class="holder__title">CA, BMS (Hons)</p>
      <ul class="contact">
        <li><span class="contact__key">E:</span>r.thornbury@vestaadvisory.co.nz</li>
        <li><span class="contact__key">P:</span>+64 21 574 613</li>
        <li><span class="contact__key">W:</span>vestaadvisory.co.nz</li>
      </ul>
    </div>
    <div class="card__band">
      <svg viewBox="0 0 700 70" preserveAspectRatio="none" aria-hidden="true">
        <rect x="0" y="44" width="700" height="26" fill="var(--brand-blue)"/>
        <path d="M540 44 L540 18 Q540 0 558 0 L700 0 L700 44 Z" fill="var(--brand-green)"/>
      </svg>
    </div>
  </section>

</main>
</body>
</html>
```